Business Card Design for a Personal Trainer

I need a business card design for my job as a personal trainer. It should have a unique, modern and exclusive design. On the front there should be only my logo with my name and my job. 0162/3819204 Tobias Lendhart Wiesengrundweg 14 80417 Munich Germany The most important contact information is the web adress. it can be bigger than the rest, but its not necessary. The card should be 8,5cmx5,5cm big. Font: Roboto. Colors: black, white, gray, 56c1ff.

```html
<!DOCTYPE html>
<html lang="de">
<head>
<meta charset="utf-8">
<title>Tobias Lendhart – Personal Trainer Business Card</title>
<link href="https://fonts.googleapis.com/css2?family=Roboto:ital,wght@0,300;0,400;0,500;1,700;1,900&display=swap" rel="stylesheet">
<style>
  :root {
    --stage: #141414;
    --card-top: #303336;
    --card-bottom: #26292c;
    --white: #ffffff;
    --text-soft: #e6e8ea;
    --ring: #b9b9b9;
    --photo-light: #3a3f43;
    --photo-dark: #1d2124;
    --accent: #56c1ff;
  }
  * { box-sizing: border-box; margin: 0; padding: 0; }
  html, body {
    width: 1189px; height: 1200px; overflow: hidden;
    background: var(--stage);
    font-family: "Roboto", Arial, sans-serif;
    color: var(--white);
  }
  .card {
    position: absolute; left: 218px; width: 752px; height: 486px;
    border-radius: 24px;
    background: linear-gradient(160deg, var(--card-top), var(--card-bottom));
    box-shadow: 0 6px 18px rgba(0,0,0,.55);
  }
  .card--front { top: 76px; }
  .card--back { top: 605px; }

  /* Front */
  .brand-mark {
    position: absolute; left: 0; right: 0; top: 186px;
    display: flex; justify-content: center; align-items: center; gap: 14px;
    font-size: 40px; font-weight: 500; letter-spacing: 4px; color: var(--white);
  }
  .brand-mark__square { width: 22px; height: 22px; background: var(--white); }

  .identity { display: inline-flex; flex-direction: column; align-items: stretch; }
  .identity__name { font-weight: 400; line-height: 1; white-space: nowrap; }
  .identity__role {
    display: flex; align-items: center; gap: 6px;
    font-weight: 400; text-transform: uppercase; color: var(--text-soft);
  }
  .identity__role::before, .identity__role::after {
    content: ""; flex: 1; height: 1.5px; background: var(--text-soft);
  }
  .card--front .identity {
    position: absolute; left: 50%; top: 280px; transform: translateX(-50%);
  }
  .card--front .identity__name { font-size: 39px; }
  .card--front .identity__role { font-size: 15px; letter-spacing: 4.5px; margin-top: 6px; }

  /* Back */
  .portrait {
    position: absolute; left: 82px; top: 120px; width: 248px; height: 248px;
    border-radius: 50%; border: 5px solid var(--ring);
    background: radial-gradient(circle at 50% 40%, var(--photo-light), var(--photo-dark) 70%);
  }
  .card--back .identity { position: absolute; left: 386px; top: 150px; }
  .card--back .identity__name { font-size: 32px; }
  .card--back .identity__role { font-size: 13px; letter-spacing: 3.6px; margin-top: 4px; }

  .contact { position: absolute; left: 386px; top: 252px; list-style: none; }
  .contact__item {
    display: flex; align-items: center; gap: 11px;
    font-size: 20px; font-weight: 300; color: var(--text-soft); height: 26px;
  }
  .contact__icon { width: 18px; height: 18px; flex: none; }
  .website {
    position: absolute; left: 386px; top: 322px;
    font-size: 20px; font-weight: 900; font-style: italic; letter-spacing: 2px;
    color: var(--white);
  }
  .website__name { color: var(--accent); font-weight: 700; }
</style>
</head>
<body>
  <section class="card card--front" aria-label="Card front">
    <div class="brand-mark"><span class="brand-mark__square"></span>LENDHART</div>
    <div class="identity">
      <h1 class="identity__name">TOBIAS LENDHART</h1>
      <p class="identity__role">Personal Trainer</p>
    </div>
  </section>

  <section class="card card--back" aria-label="Card back">
    <div class="portrait" role="img" aria-label="Black and white portrait photo of the trainer"></div>
    <div class="identity">
      <h2 class="identity__name">TOBIAS LENDHART</h2>
      <p class="identity__role">Personal Trainer</p>
    </div>
    <ul class="contact">
      <li class="contact__item">
        <svg class="contact__icon" viewBox="0 0 24 24" aria-hidden="true"><path fill="#56c1ff" d="M6.6 10.8a15 15 0 0 0 6.6 6.6l2.2-2.2a1 1 0 0 1 1-.25 11.4 11.4 0 0 0 3.6.57 1 1 0 0 1 1 1V20a1 1 0 0 1-1 1A17 17 0 0 1 3 4a1 1 0 0 1 1-1h3.5a1 1 0 0 1 1 1c0 1.25.2 2.45.57 3.57a1 1 0 0 1-.25 1z"/></svg>
        0162/3819204
      </li>
      <li class="contact__item">
        <svg class="contact__icon" viewBox="0 0 24 24" aria-hidden="true"><rect x="1" y="4" width="22" height="16" fill="#56c1ff"/><path d="M1 4l11 9 11-9" fill="none" stroke="#26292c" stroke-width="2"/></svg>
        info@lendhart-fit.de
      </li>
    </ul>
    <p class="website">www.<span class="website__name">LENDHARTFIT</span>.com</p>
  </section>
</body>
</html>
```